Healthcare website

We want to replace our website using joomla as the CMS. We want it to be device agnostic (gantry etc). Our business is health care our clients are people with high level spinal cord injuries ( quadriplegia / tetraplegia etc ). The site is a marketing tool primarily to potential clients and a portal for existing staff to access forms etc. It will showcase our key staff and our capability. It will also be where any new recruits apply to work with us. It must allow us to integrate our social media initiatives also. The final design must convey sophistication, high quality care and be warm and welcoming.

current web site is www.tendralwick.com.au
Updates

I have made small change to the brief in that i have removed the prefered color and indicated it would be nice to see some images that symbolize change / transformation like butterflies etc. thank you

Target Market(s)

Our business is health care our clients are people with high level spinal cord injuries ( quadriplegia / tetraplegia etc ).

Industry/Entity Type

Marketing

Colors

Designer to choose colors to be used in the design.

Requirements
Must have
• The site is a marketing tool primarily to potential clients and a portal for existing staff to access forms etc. It will showcase our key staff and our capability. It will also be where any new recruits apply to work with us. It must allow us to integrate our social media initiatives also. The final design must convey sophistication, high quality care and be warm and welcoming.
Nice to have
• Would be nice to incorporate images that symbolize change and new transformations - butterflies etc.

```html
<!DOCTYPE html>
<html lang="en">
<head>
<meta charset="utf-8">
<title>Tendralwick Care</title>
<link href="https://fonts.googleapis.com/css2?family=Arimo:wght@400;700&display=swap" rel="stylesheet">
<style>
:root{
  --blue:#2b6db5;
  --navy:#0b1f4a;
  --band:#4a4a4a;
  --grey-bg:#e4e7ea;
  --text:#555;
  --dark:#222;
  --footer:#3a3a3a;
  --footer-bottom:#2f2f2f;
  --footer-text:#a9a9a9;
  --white:#fff;
}
*{box-sizing:border-box;margin:0;padding:0}
html,body{width:674px;height:1200px;overflow:hidden;background:var(--white);font-family:"Arimo",Arial,sans-serif;color:var(--text)}
.page{position:relative;width:674px;height:1200px}
section,header,footer{position:absolute;left:0;width:674px}

/* header */
.site-header{top:0;height:45px;background:var(--white);border-bottom:1px solid #ddd}
.brand{position:absolute;left:97px;top:12px;display:flex;align-items:center;gap:5px;font-size:13px;font-weight:700;color:var(--blue)}
.brand-dot{width:14px;height:14px;border-radius:50%;background:var(--blue)}
.main-nav{position:absolute;right:100px;top:19px;display:flex;gap:36px;font-size:6.5px;color:#666;letter-spacing:.2px}

/* hero */
.hero{top:45px;height:212px;background:radial-gradient(ellipse at 40% 45%,#4f6fc0 0%,#1c3c8a 35%,var(--navy) 80%)}
.hero-art{position:absolute;left:0;top:0;width:380px;height:212px;background:radial-gradient(ellipse at 70% 55%,rgba(200,80,190,.55) 0%,rgba(120,150,230,.25) 35%,transparent 70%)}
.hero-copy{position:absolute;left:390px;top:50px;width:215px;color:var(--white)}
.hero-copy h1{font-size:19px;font-weight:700;line-height:1.1;letter-spacing:.3px}
.hero-copy h2{font-size:15px;font-weight:400;margin-top:3px}
.hero-copy .lead{font-size:7.8px;line-height:1.5;margin-top:8px}
.hero-copy .body{font-size:5.6px;line-height:1.95;margin-top:6px}
.hero-arrow{position:absolute;top:92px;width:10px;height:26px}

/* join band */
.join{top:257px;height:52px;background:var(--band);color:var(--white)}
.join h3{position:absolute;left:97px;top:12px;font-size:9.5px;font-weight:400}
.join p{position:absolute;left:97px;top:30px;font-size:5.8px;color:#ddd}
.join-btn{position:absolute;left:472px;top:15px;width:93px;height:22px;border:1px solid var(--white);font-size:6.5px;display:flex;align-items:center;justify-content:center}

.section-title{text-align:center;color:var(--blue);font-size:12.5px;font-weight:400;letter-spacing:.4px}

/* services */
.services{top:309px;height:249px}
.services .section-title{margin-top:26px}
.service{position:absolute;top:56px;width:149px}
.service .photo{width:149px;height:83px}
.service h4{font-size:6.8px;color:var(--blue);font-weight:400;margin-top:10px}
.service p{font-size:5.5px;line-height:2.2;margin-top:5px;color:#555}
.read-more{display:inline-block;margin-top:8px;border:1px solid var(--blue);color:var(--blue);font-size:5.2px;padding:4px 9px}

/* team */
.team{top:558px;height:276px;background:var(--grey-bg)}
.team .section-title{margin-top:23px}
.team-intro{width:460px;margin:11px auto 0;text-align:center;font-size:5.5px;line-height:2.2;color:#666}
.member{position:absolute;top:104px;width:119px;text-align:center}
.member .photo{width:119px;height:110px}
.member h5{font-size:6.8px;font-weight:400;color:var(--dark);margin-top:9px}
.member span{display:block;font-size:5.6px;font-style:italic;color:#666;margin-top:5px}
.slider-arrow{position:absolute;width:6px;height:16px}

/* news */
.news{top:834px;height:180px}
.news .section-title{margin-top:28px}
.news-intro{text-align:center;font-size:6.5px;color:#555;margin-top:12px}
.news-item{position:absolute;top:90px;display:flex;gap:15px}
.news-item .photo{width:85px;height:56px;border:1px solid #ddd}
.news-item h6{width:145px;font-size:6.2px;font-weight:400;line-height:1.9;color:var(--dark)}
.news-item em{display:block;font-size:5.2px;color:#666;margin-top:5px}

/* footer */
.site-footer{top:1014px;height:159px;background:var(--footer);color:var(--footer-text)}
.footer-col{position:absolute;top:20px;font-size:5.6px;line-height:2.35}
.footer-col h6{font-size:6.5px;color:var(--white);font-weight:400;margin-bottom:4px;line-height:1.4}
.social-row{display:flex;align-items:center;gap:6px;margin-top:5px}
.social-box{width:15px;height:15px;border:1px solid #666}
.partner-badges{position:absolute;left:184px;top:126px;display:flex;gap:12px;align-items:center}
.badge{background:#cfcfcf}
.copyright{position:absolute;left:0;top:1173px;width:674px;height:27px;background:var(--footer-bottom);color:#999;font-size:5.8px;text-align:center;line-height:27px}
</style>
</head>
<body>
<div class="page">

<header class="site-header">
  <div class="brand"><span>Tendralwick</span><span class="brand-dot"></span></div>
  <nav class="main-nav"><span>HOME</span><span>ABOUT US</span><span>OUR SERVICES</span><span>RESOURCES</span><span>CONTACT US</span></nav>
</header>

<section class="hero">
  <div class="hero-art" role="img" aria-label="Glowing blue x-ray illustration of a human torso with the spine highlighted in magenta"></div>
  <svg class="hero-arrow" style="left:46px" viewBox="0 0 10 26"><path d="M8 1 L2 13 L8 25" fill="none" stroke="rgba(255,255,255,.35)" stroke-width="1"/></svg>
  <svg class="hero-arrow" style="left:620px" viewBox="0 0 10 26"><path d="M2 1 L8 13 L2 25" fill="none" stroke="rgba(255,255,255,.35)" stroke-width="1"/></svg>
  <div class="hero-copy">
    <h1>TENDRALWICK</h1>
    <h2>is a small team of care</h2>
    <p class="lead">We are a high level spinal cord injuries treatment center ( quadriplegia / tetraplegia etc )</p>
    <p class="body">Tendralwick Care has built its service around the needs of each and every client. We listen to and consult with our clients, their families, Care Teams and the wider care community.</p>
  </div>
</section>

<section class="join">
  <h3>JOIN OUR TEAM</h3>
  <p>We are always on the lookout for great people to work with our clients, If you want to be a part of our Team click below to apply.</p>
  <div class="join-btn">JOIN OUR TEAM</div>
</section>

<section class="services">
  <h2 class="section-title">OUR SERVICES</h2>
  <div class="service" style="left:97px">
    <div class="photo" role="img" aria-label="Photo of a carer assisting an older man with shoulder exercises" style="background:linear-gradient(135deg,#e9e6e2,#b9aca0)"></div>
    <h4>ATTENDANT CARE</h4>
    <p>As Founder of Tendralwick Care, I am reminded daily of the extraordinary dedication, committment, and level of compassion our team members...</p>
    <span class="read-more">READ MORE</span>
  </div>
  <div class="service" style="left:263px">
    <div class="photo" role="img" aria-label="Blue medical illustration of a human back and spine" style="background:radial-gradient(circle at 40% 50%,#5f86d0,#102a66 75%)"></div>
    <h4>SPINAL CARE - SCI</h4>
    <p>As Founder of Tendralwick Care, I am reminded daily of the extraordinary dedication, committment, and level of compassion our team members...</p>
    <span class="read-more">READ MORE</span>
  </div>
  <div class="service" style="left:429px">
    <div class="photo" role="img" aria-label="Photo of a smiling woman and older man stretching together" style="background:linear-gradient(135deg,#d8c7b8,#7c8fa8)"></div>
    <h4>REFERRAL</h4>
    <p>As Founder of Tendralwick Care, I am reminded daily of the extraordinary dedication, committment, and level of compassion our team members...</p>
    <span class="read-more">READ MORE</span>
  </div>
</section>

<section class="team">
  <h2 class="section-title">OUR TEAM</h2>
  <p class="team-intro">As Founder of Tendralwick Care, I am reminded daily of the extraordinary dedication, committment, and level of compassion our team members demonstrate, not only to those they provide for, but also to the benefit of the team. It is both a personal and professional privilege to be able to provide them the support and resources they need to to attend to those for which they have dedicated their hearts and souls.</p>
  <svg class="slider-arrow" style="left:68px;top:157px" viewBox="0 0 6 16"><path d="M5 1 L1 8 L5 15" fill="none" stroke="#888" stroke-width="0.8"/></svg>
  <svg class="slider-arrow" style="left:598px;top:157px" viewBox="0 0 6 16"><path d="M1 1 L5 8 L1 15" fill="none" stroke="#888" stroke-width="0.8"/></svg>
  <div class="member" style="left:97px">
    <div class="photo" role="img" aria-label="Portrait of team member Mark Ellery, with profile link overlay" style="background:#6e6e6e;display:flex;align-items:center;justify-content:center">
      <svg width="17" height="17" viewBox="0 0 17 17"><circle cx="8.5" cy="8.5" r="8.5" fill="#fff" fill-opacity=".85"/><path d="M6 11 L11 6" stroke="#666" stroke-width="1.4"/></svg>
    </div>
    <h5>Mark Ellery</h5><span>Click here for View Profile</span>
  </div>
  <div class="member" style="left:217px">
    <div class="photo" role="img" aria-label="Portrait of team member Lena Marsh" style="background:linear-gradient(180deg,#fff 30%,#d9c2b0 70%,#3d5fa8)"></div>
    <h5>Lena Marsh</h5><span>Click here for View Profile</span>
  </div>
  <div class="member" style="left:337px">
    <div class="photo" role="img" aria-label="Portrait of team member Gina Corell" style="background:linear-gradient(180deg,#fff 20%,#c28a62 55%,#7a3a4a)"></div>
    <h5>Gina Corell</h5><span>Click here for View Profile</span>
  </div>
  <div class="member" style="left:457px">
    <div class="photo" role="img" aria-label="Portrait of team member Ruth Kaling" style="background:linear-gradient(180deg,#fff 25%,#d8b690 60%,#3a3a3a)"></div>
    <h5>Ruth Kaling</h5><span>Chief Executive Officer</span>
  </div>
</section>

<section class="news">
  <h2 class="section-title">LATEST NEWS</h2>
  <p class="news-intro">The latest Spinal Cord Injury News, Information and Resources for People living with SCI Spinal Cord Injury</p>
  <svg class="slider-arrow" style="left:68px;top:109px" viewBox="0 0 6 16"><path d="M5 1 L1 8 L5 15" fill="none" stroke="#888" stroke-width="0.8"/></svg>
  <svg class="slider-arrow" style="left:598px;top:109px" viewBox="0 0 6 16"><path d="M1 1 L5 8 L1 15" fill="none" stroke="#888" stroke-width="0.8"/></svg>
  <article class="news-item" style="left:99px">
    <div class="photo" role="img" aria-label="Photo of hands massaging a bare shoulder" style="background:linear-gradient(135deg,#f3e3d6,#c98f6c)"></div>
    <div><h6>New Methods Show Promise for Rehabilitating Paralyzed Patients With Spinal Cord Injury</h6><em>Posted on 27 march 2014</em></div>
  </article>
  <article class="news-item" style="left:349px">
    <div class="photo" role="img" aria-label="Photo of a person holding their lower back" style="background:linear-gradient(180deg,#a7bbd6,#d6b39a 60%,#333)"></div>
    <div><h6>New Methods Show Promise for Rehabilitating Paralyzed Patients With Spinal Cord Injury</h6><em>Posted on 27 march 2014</em></div>
  </article>
</section>

<footer class="site-footer">
  <div class="footer-col" style="left:97px">
    <h6>LICENSED.</h6>
    Home<br>About Us<br>Our Services<br>Resources<br>Contact Us
  </div>
  <div class="footer-col" style="left:184px;width:150px">
    <h6>LICENSED</h6>
    Tendralwick Care is proud to be an approved provider for Road Recovery Commission (RRC), State Workplace Cover Office (SWCO), Office of Community Services (OCS) and maintain associations and cooperative relationships with a variety of private and governmental organisations in its efforts to bring the finest, most up-to-date care for its clients.
  </div>
  <div class="footer-col" style="left:376px">
    <h6>CONTACT US</h6>
    42 - 44 Alder Grove Rd<br>Fernleigh<br>Victoria, 3999<br>Call Us : (03) 9000 4172
  </div>
  <div class="footer-col" style="left:494px">
    <h6>FOLLOW US :</h6>
    Connect with our social network!
    <div class="social-row"><span class="social-box"></span>: Friendbook</div>
    <div class="social-row"><span class="social-box"></span>: Chirper</div>
    <div class="social-row"><span class="social-box"></span>: Linkpro</div>
    <div class="social-row"><span class="social-box"></span>: Vidstream</div>
  </div>
  <div class="partner-badges">
    <span class="badge" style="width:26px;height:20px"></span>
    <span class="badge" style="width:14px;height:18px"></span>
    <span class="badge" style="width:46px;height:14px"></span>
    <span class="badge" style="width:13px;height:15px"></span>
    <span class="badge" style="width:52px;height:12px"></span>
    <span class="badge" style="width:14px;height:22px"></span>
  </div>
</footer>
<div class="copyright">© 2014. Tendralwick Care. All rights reserved.</div>

</div>
</body>
</html>
```